Kestrelway Financial Plans

I am looking for a complete resdesign of my small financial presentation. This is a Word Doc/PDF that I print off when meeting with people in private. I often present my "two pager" that I have been using for years and years. It tells them the basics of what I do, how I help people and foundational financial principles.

I have recently gone out on my own in business and have completely rebranded. This presentation is my most used tool, so it is the first of many things I would like to redo. I am hoping it will somehow coordinate with the colors of my business, not necessarily the EXACT same 3 colors everywhere, but have the design colors compliment.

I've uploaded all my logo designs, as well as the current "two-pager". I am not against it going to 3 pages if needed. As it will still land on 2 pages with duplex printing.

It has always been VERY simple. I am wanting it built into a more professional and design specific format, to show off my branding, without being over cluttered.

I am completely open to ANY graphics changes. Obviously some are very novice, the house on the last page has always been overly simplified.

```html
<!DOCTYPE html>
<html lang="en">
<head>
<meta charset="utf-8">
<title>Kestrelway Financial Plans – The Financial Challenge</title>
<link href="https://fonts.googleapis.com/css2?family=Montserrat:wght@400;600;800&family=Open+Sans:wght@400;600&display=swap" rel="stylesheet">
<style>
:root{
  --green:#2f9d4b;
  --green-dark:#1d7a37;
  --lime:#8dc63f;
  --ink:#1f2a2e;
  --grey:#6b7378;
  --paper:#ffffff;
  --backdrop:#e9ebec;
  --pale:#eef5ef;
}
*{box-sizing:border-box;margin:0;padding:0}
html,body{width:882px;height:1200px;overflow:hidden;background:var(--backdrop)}
body{position:relative;font-family:"Open Sans",sans-serif;color:var(--ink)}
.spread{position:absolute;top:328px;left:12px;display:flex;gap:18px}
.page{position:relative;width:420px;height:544px;background:var(--paper);box-shadow:0 4px 14px rgba(0,0,0,.15);overflow:hidden}
.brand{position:absolute;top:22px;left:22px;font-family:"Montserrat",sans-serif}
.brand-name{font-weight:800;font-size:20px;letter-spacing:.5px;color:var(--ink);display:flex;align-items:center;gap:6px}
.brand-name i{width:10px;height:10px;background:var(--green);display:inline-block}
.brand-sub{font-size:7px;letter-spacing:2px;color:var(--green);font-weight:600;margin-left:16px}
.hero-art{position:absolute;top:14px;right:18px;width:150px;height:64px;border-radius:6px;background:linear-gradient(135deg,#f4d47a,#9fd08a 60%,#5ab0d8)}
.title-band{position:absolute;top:86px;left:0;width:270px;height:44px;background:var(--ink);padding:7px 22px}
.title-band small{display:block;font-family:"Montserrat",sans-serif;font-size:8px;color:#fff;letter-spacing:2px;line-height:1.2}
.title-band h1{font-family:"Montserrat",sans-serif;font-size:16px;font-weight:800;color:var(--lime);letter-spacing:.3px;line-height:1.2;white-space:nowrap}
.pillars{position:absolute;top:142px;left:22px;right:22px;display:flex;gap:14px}
.pillar{flex:1}
.pillar h2{font-family:"Montserrat",sans-serif;font-size:11px;font-weight:800;color:var(--green);margin-bottom:4px}
.pillar ul{list-style:none;font-size:5.6px;line-height:1.5;color:var(--grey)}
.pillar li::before{content:"■ ";color:var(--green)}
.icon-row{position:absolute;top:228px;left:22px;right:22px;display:flex;justify-content:space-between}
.icon-row div{width:52px;text-align:center;font-size:5px;color:var(--grey)}
.icon-row svg{display:block;margin:0 auto 2px}
.who-band{position:absolute;top:262px;left:0;right:0;height:22px;background:var(--green);color:#fff;font-family:"Montserrat",sans-serif;font-size:10px;font-weight:800;text-align:center;line-height:22px}
.how{position:absolute;top:292px;left:0;right:0;text-align:center;font-family:"Montserrat",sans-serif;font-size:10px;font-weight:800;color:var(--ink)}
.pie{position:absolute;top:310px;left:22px}
.savings-arc{position:absolute;top:308px;left:216px}
.savings-list{position:absolute;top:326px;left:302px;list-style:none;font-size:7px;font-weight:600;line-height:2.1;color:var(--ink)}
.savings-list li::before{content:"";display:inline-block;width:6px;height:6px;background:var(--green);margin-right:5px}
.foot{position:absolute;bottom:14px;right:22px;font-size:6px;color:var(--green);font-weight:600}

.photo{position:absolute;top:0;left:0;right:0;height:170px;background:linear-gradient(160deg,#cfd8d6,#8fa39c 55%,#4b5d58)}
.rule{position:absolute;top:18px;right:18px;width:150px;background:rgba(255,255,255,.92);padding:6px 8px}
.rule h2{font-family:"Montserrat",sans-serif;font-size:11px;font-weight:800;color:var(--green);text-align:center;margin-bottom:4px}
.rule table{width:100%;border-collapse:collapse;font-size:6px}
.rule th{background:var(--ink);color:#fff;padding:2px}
.rule td{padding:2px;text-align:center;border-bottom:1px solid #dde}
.rule tr:nth-child(even) td{background:var(--pale)}
.doubling{position:absolute;top:182px;left:18px;right:18px;display:flex;gap:8px}
.doubling div{flex:1;height:62px;background:var(--green);color:#fff;font-family:"Montserrat",sans-serif;font-weight:800;font-size:11px;line-height:1.15;text-align:center;padding-top:14px}
.doubling div:nth-child(even){background:var(--green-dark)}
.house{position:absolute;top:262px;left:18px}
.umbrella{position:absolute;top:282px;left:160px;width:100px;height:46px;border-radius:50px 50px 4px 4px;background:linear-gradient(#d8efd9,#a6d7a8)}
.house-label{position:absolute;font-family:"Montserrat",sans-serif;font-weight:800;color:var(--ink);font-size:9px}
.house-label small{display:block;font-family:"Open Sans",sans-serif;font-weight:400;font-size:5.5px;color:var(--grey)}
</style>
</head>
<body>
<div class="spread">

  <section class="page page-challenge">
    <div class="brand">
      <div class="brand-name"><i></i>KESTRELWAY</div>
      <div class="brand-sub">FINANCIAL PLANS</div>
    </div>
    <div class="hero-art" role="img" aria-label="Illustration of people with coins, money and savings symbols"></div>

    <div class="title-band">
      <small>THE</small>
      <h1>FINANCIAL CHALLENGE</h1>
    </div>

    <div class="pillars">
      <div class="pillar">
        <h2>SAVINGS</h2>
        <ul>
          <li>Most families save less than they plan each year</li>
          <li>Rising costs shrink the money set aside</li>
          <li>Few have a clear long term goal</li>
        </ul>
      </div>
      <div class="pillar">
        <h2>DEBT</h2>
        <ul>
          <li>Household debt keeps growing faster than income</li>
          <li>High interest slows every other goal</li>
          <li>Many carry balances month to month</li>
        </ul>
      </div>
      <div class="pillar">
        <h2>INSURANCE</h2>
        <ul>
          <li>Many homes are under protected today</li>
          <li>Illness can stop income without warning</li>
          <li>Coverage is often left unreviewed</li>
        </ul>
      </div>
    </div>

    <div class="icon-row">
      <div><svg width="22" height="16" viewBox="0 0 22 16"><path d="M2 8 11 1l9 7v7H2z" fill="var(--green)"/></svg>Home</div>
      <div><svg width="22" height="16" viewBox="0 0 22 16"><rect x="2" y="3" width="18" height="11" rx="2" fill="var(--ink)"/><rect x="2" y="6" width="18" height="2" fill="var(--lime)"/></svg>Credit</div>
      <div><svg width="22" height="16" viewBox="0 0 22 16"><path d="M1 8a10 7 0 0 1 20 0z" fill="var(--green)"/><path d="M11 8v6" stroke="var(--ink)" stroke-width="1.5"/></svg>Protect</div>
      <div><svg width="22" height="16" viewBox="0 0 22 16"><rect x="3" y="8" width="4" height="7" fill="var(--lime)"/><rect x="9" y="5" width="4" height="10" fill="var(--green)"/><rect x="15" y="2" width="4" height="13" fill="var(--ink)"/></svg>Growth</div>
      <div><svg width="22" height="16" viewBox="0 0 22 16"><ellipse cx="11" cy="9" rx="8" ry="6" fill="var(--green)"/><rect x="9" y="2" width="4" height="2" fill="var(--ink)"/></svg>Savings</div>
    </div>

    <div class="who-band">WHO ARE WE AND WHAT DO WE DO?</div>
    <div class="how">HOW ARE WE DOING IT?</div>

    <svg class="pie" width="190" height="200" viewBox="0 0 190 200" role="img" aria-label="Pie chart of how income is divided">
      <g transform="translate(95 100)">
        <path d="M0 0 L0 -80 A80 80 0 0 1 76 -25 Z" fill="var(--ink)"/>
        <path d="M0 0 L76 -25 A80 80 0 0 1 40 69 Z" fill="var(--green)"/>
        <path d="M0 0 L40 69 A80 80 0 0 1 -69 40 Z" fill="#d6dadc"/>
        <path d="M0 0 L-69 40 A80 80 0 0 1 0 -80 Z" fill="var(--lime)"/>
        <text x="22" y="-40" font-size="7" fill="#fff" font-family="Montserrat,sans-serif" font-weight="600">SAVE</text>
        <text x="30" y="12" font-size="7" fill="#fff" font-family="Montserrat,sans-serif" font-weight="600">DEBT</text>
        <text x="-22" y="45" font-size="7" fill="var(--ink)" font-family="Montserrat,sans-serif" font-weight="600">LIVING</text>
        <text x="-52" y="-12" font-size="7" fill="var(--ink)" font-family="Montserrat,sans-serif" font-weight="600">TAX</text>
      </g>
    </svg>

    <svg class="savings-arc" width="80" height="200" viewBox="0 0 80 200">
      <path d="M70 0 Q-30 100 70 200 L80 200 L80 0z" fill="var(--green)"/>
      <text transform="translate(60 100) rotate(-90)" text-anchor="middle" font-family="Montserrat,sans-serif" font-weight="800" font-size="16" fill="#fff">SAVINGS</text>
    </svg>
    <ul class="savings-list">
      <li>Retirement Saving</li>
      <li>Children's Education</li>
      <li>Group Protection</li>
      <li>Emergency Fund</li>
      <li>Market Protection</li>
    </ul>
    <div class="foot">kestrelway.example</div>
  </section>

  <section class="page page-growth">
    <div class="photo" role="img" aria-label="Photo of a desk with calculator and paperwork"></div>
    <div class="rule">
      <h2>RULE OF 72</h2>
      <table>
        <tr><th>Rate</th><th>Years</th><th>Growth</th></tr>
        <tr><td>4%</td><td>18</td><td>$20,000</td></tr>
        <tr><td>6%</td><td>12</td><td>$40,000</td></tr>
        <tr><td>8%</td><td>9</td><td>$80,000</td></tr>
        <tr><td>12%</td><td>6</td><td>$160,000</td></tr>
      </table>
    </div>

    <div class="doubling">
      <div>EVERY<br>18<br>YEARS</div>
      <div>EVERY<br>12<br>YEARS</div>
      <div>EVERY<br>9<br>YEARS</div>
      <div>EVERY<br>6<br>YEARS</div>
    </div>

    <svg class="house" width="384" height="260" viewBox="0 0 384 260">
      <path d="M192 6 L372 110 L12 110 Z" fill="none" stroke="var(--green)" stroke-width="5" stroke-linejoin="round"/>
      <rect x="36" y="110" width="312" height="140" fill="none" stroke="var(--ink)" stroke-width="3"/>
      <rect x="160" y="84" width="64" height="20" rx="3" fill="var(--ink)"/>
      <text x="192" y="98" text-anchor="middle" font-family="Montserrat,sans-serif" font-weight="800" font-size="10" fill="#fff">TAXES</text>
      <line x1="192" y1="110" x2="192" y2="250" stroke="var(--green)" stroke-width="2"/>
      <line x1="36" y1="206" x2="348" y2="206" stroke="var(--green)" stroke-width="2"/>
    </svg>
    <div class="umbrella" role="img" aria-label="Illustration of an umbrella sheltering a family home"></div>

    <div class="house-label" style="top:380px;left:66px">HOME<small>Mortgage plan</small></div>
    <div class="house-label" style="top:406px;left:66px">WILL<small>Estate wishes</small></div>
    <div class="house-label" style="top:432px;left:66px">TFSA / RRSP<small>Tax sheltered growth</small></div>
    <div class="house-label" style="top:380px;left:222px">LIFE INSURANCE<small>Family protection</small></div>
    <div class="house-label" style="top:406px;left:222px">ILLNESS<small>Critical care cover</small></div>
    <div class="house-label" style="top:432px;left:222px">DISABILITY<small>Income protection</small></div>
    <div class="house-label" style="top:478px;left:66px">DEBT MANAGEMENT</div>
    <div class="house-label" style="top:478px;left:222px">CASH FLOW</div>
  </section>

</div>
</body>
</html>
```